New Business card design to reflect rebrand

I would like a business card design with a good base colour for our new logo and also a placeholder for a profile pic of the card holder. the design needs to be editable to the point that we can easily change the picture of the person and use that design for printmerlo etc. we are looking at a metalic finish business card so will need a good base colour to bring out the finish.

Target Market(s)

prospective customers

Industry/Entity Type

Business

Contact Information for Business Card

I would like one editable design that we can change the name of the card holder and profile picture. The design need to be in a format that be send to printmerlo etc.

Our address is Fenwick Lodge, Copse Lane, Ashcombe Vale, GU14 3TP Tel no. 01483 556172

Requirements
Must have
• place holder for a profile pic for the card holder. in AI or preferably PSD format

```html
<!DOCTYPE html>
<html lang="en">
<head>
<meta charset="utf-8">
<title>Corvane Workplace Services – Business Card</title>
<link rel="stylesheet" href="https://fonts.googleapis.com/css2?family=Michroma&family=PT+Sans&display=swap">
<style>
  :root {
    --page-bg: #e9e6e1;
    --card-black: #0c0c0d;
    --card-charcoal: #1d1d20;
    --accent-orange: #ee6206;
    --accent-slate: #4f6a85;
    --text-white: #f2f2f2;
    --text-soft: #d9d9d9;
    --photo-tone-a: #5a4a42;
    --photo-tone-b: #2a2c36;
  }
  * { box-sizing: border-box; margin: 0; padding: 0; }
  html, body { width: 1200px; height: 900px; overflow: hidden; }
  body {
    background: var(--page-bg);
    position: relative;
    font-family: "PT Sans", sans-serif;
  }
  .card {
    position: absolute;
    width: 520px;
    height: 336px;
    border-radius: 4px;
    overflow: hidden;
    background: radial-gradient(ellipse at 40% 30%, var(--card-charcoal), var(--card-black) 75%);
    box-shadow: 0 10px 28px rgba(0,0,0,0.25);
  }
  .card--front { left: 60px; top: 282px; }
  .card--back  { left: 620px; top: 282px; }

  /* Front: company name */
  .brand {
    position: absolute;
    inset: 0;
    display: flex;
    flex-direction: column;
    align-items: center;
    justify-content: center;
    color: var(--text-white);
    font-family: "Michroma", sans-serif;
    font-weight: 400;
    text-align: center;
  }
  .brand__name { font-size: 46px; letter-spacing: 2px; line-height: 1.1; }
  .brand__tagline { font-size: 17px; letter-spacing: 6px; margin-top: 10px; }

  /* Back: contact side */
  .holder-photo {
    position: absolute;
    left: 330px;
    top: 16px;
    width: 170px;
    height: 190px;
    background: linear-gradient(160deg, var(--photo-tone-a), var(--photo-tone-b));
  }
  .wave { position: absolute; left: 0; top: 0; width: 520px; height: 336px; }
  .holder-name {
    position: absolute;
    left: 36px;
    top: 118px;
    font-family: "Michroma", sans-serif;
    font-size: 17px;
    letter-spacing: 1.5px;
    white-space: nowrap;
  }
  .holder-name__first { color: var(--accent-orange); }
  .holder-name__last { color: var(--accent-slate); }
  .contact {
    position: absolute;
    left: 36px;
    top: 168px;
    color: var(--text-soft);
    font-size: 14px;
    line-height: 1.45;
    list-style: none;
    white-space: nowrap;
  }
  .contact__item { display: flex; align-items: center; gap: 7px; }
  .contact__icon { width: 11px; height: 11px; fill: var(--accent-orange); flex: none; }
  .contact__address { margin-top: 6px; }
</style>
</head>
<body>

  <section class="card card--front" aria-label="Business card front">
    <div class="brand">
      <span class="brand__name">CORVANE</span>
      <span class="brand__tagline">WORKPLACE SERVICES</span>
    </div>
  </section>

  <section class="card card--back" aria-label="Business card back">
    <div class="holder-photo" role="img" aria-label="Profile photo of the card holder"></div>
    <svg class="wave" viewBox="0 0 520 336" aria-hidden="true">
      <path d="M0 290 C120 300 220 260 300 232 C380 204 440 190 520 176 L520 336 L0 336 Z" fill="var(--accent-slate)"/>
      <path d="M0 300 C120 308 220 272 300 246 C380 220 440 208 520 196 L520 336 L0 336 Z" fill="var(--card-black)"/>
      <path d="M0 318 C130 318 230 270 300 236 C360 206 420 170 520 170 L520 336 L0 336 Z" fill="var(--accent-orange)"/>
      <path d="M300 236 C360 206 420 170 520 170 L520 176 C440 190 380 204 300 232 Z" fill="var(--accent-orange)"/>
    </svg>
    <p class="holder-name"><span class="holder-name__first">DANIEL</span> <span class="holder-name__last">HART</span></p>
    <ul class="contact">
      <li class="contact__item">
        <svg class="contact__icon" viewBox="0 0 24 24" aria-hidden="true"><path d="M6.6 10.8a15 15 0 0 0 6.6 6.6l2.2-2.2a1 1 0 0 1 1-.25 11.4 11.4 0 0 0 3.6.57 1 1 0 0 1 1 1V20a1 1 0 0 1-1 1A17 17 0 0 1 3 4a1 1 0 0 1 1-1h3.5a1 1 0 0 1 1 1c0 1.25.2 2.45.57 3.6a1 1 0 0 1-.25 1z"/></svg>
        01483 556172
      </li>
      <li class="contact__item">
        <svg class="contact__icon" viewBox="0 0 24 24" aria-hidden="true"><path d="M2 5h20v14H2z M2 5l10 8 10-8" /></svg>
        info@corvane.co.uk
      </li>
      <li class="contact__address">Fenwick Lodge, Copse Lane,<br>Ashcombe Vale, GU14 3TP</li>
    </ul>
  </section>

</body>
</html>
```